Web site for a company that sells Pinball machines

We need a website that is an online shopping experience for a Store that sells pinball machines and accessories. The name of the store is called "Gadget Arcade." The store it self has a showroom, but we would also like to have an Internet e-commerce presence. We pinball machines made by Vexler pinball. You can visit their website and see their current list of machines as well as their website for the machines that we are going to carry in our store. Their website is Vexlerpinball.com. I am able to use their machine photos as well as their machine brochure PDF files. I am also able to use their logo on my website two list it as a Vexler Authorized Dealer.
This website design needs to be funky, fun, very technologically oriented and modern. The people buying machines our spending anywhere between $5000 and $15,000 on one machine. These Are high-end buyers who are also usually fairly tech savvy or at least enjoy technology and graphics.
Attachments: I have attached photographs of some of my own machines which may be used in the website. I've also attached some downloaded files from Vexler pinball.com as well as some of their PDF files for brochures. I will carry all of their current models they have listed under games. Not the archived games. I have included one of their machines called Thunderwolf Limited edition in my photograph attachments. The rest of the photos are just random pictures that I have taken myself and maybe used to build the site. Lastly I have attached my logo which I am not super crazy about so I will also be posting a contest to redesign this logo. Tons more of my own pinball photos are available.
I would like for people to be able to purchase machines and accessories from the website, but also inform them to our actual showroom.
Updates
Project Deadline Extended Reason: Hello. We have extended five days due to some complications during the construction of our actual building. We were unable to participate in this web design during this time and so unfortunately were not able give feedback appropriately. We are back on track and will provide feedback to the designers who have designed up until this point. We will still be interested in seeing new submissions, however; this extension will give us a chance to provide feedback and coordinate the website appropriately. Thank you so much for your submissions and your patience!!!!Gadget Arcade Added Friday, April 21, 2017
Target Market(s)
Target market is 16 to 75. Techy individuals to enjoy gaming technology video animation and Vegas style twinkle
Industry/Entity Type
It Company
Coding
Coded - Design and coding required
Number of Pages Required
3 page
Font styles to use
Look and feel
Each slider illustrates characteristics of the customer's brand and the style your logo design should communicate.

```html
<!DOCTYPE html>
<html lang="en">
<head>
<meta charset="utf-8">
<title>Gadget Arcade</title>
<link href="https://fonts.googleapis.com/css2?family=Oswald:wght@400;500;600&family=Lato:wght@400;700&display=swap" rel="stylesheet">
<style>
  :root {
    --red: #c4121c;
    --red-dark: #8e0a12;
    --red-deep: #6f070d;
    --white: #ffffff;
    --ink: #1d1d1d;
    --grey: #6b6b6b;
    --footer: #111111;
    --footer-line: #2b2b2b;
  }
  * { box-sizing: border-box; margin: 0; padding: 0; }
  html, body { width: 1200px; height: 3905px; overflow: hidden; }
  body { font-family: "Lato", sans-serif; color: var(--ink); background: #222; }
  .page { position: relative; width: 1200px; height: 3905px; overflow: hidden; }
  .abs { position: absolute; }

  /* Header */
  .site-header {
    position: absolute; left: 0; top: 0; width: 1200px; height: 70px;
    background: linear-gradient(#d0141f, var(--red-dark));
    border-bottom: 3px solid var(--red-deep); z-index: 5;
  }
  .nav-link {
    position: absolute; top: 30px; font-family: "Oswald", sans-serif; font-weight: 500;
    font-size: 13px; color: var(--white); letter-spacing: .3px; text-transform: uppercase;
  }
  .brand {
    position: absolute; left: 535px; top: 8px; width: 130px;
    display: flex; flex-direction: column; align-items: center; gap: 3px;
  }
  .brand-mark { width: 40px; height: 40px; border-radius: 50%; background: var(--white); border: 3px solid #d9d9d9; }
  .brand-name { font-family: "Oswald", sans-serif; font-weight: 500; font-size: 13px; color: var(--white); letter-spacing: .5px; white-space: nowrap; }
  .cart { display: flex; align-items: center; gap: 7px; }

  /* Hero */
  .hero {
    position: absolute; left: 0; top: 70px; width: 1200px; height: 542px;
    background:
      linear-gradient(rgba(0,0,0,.25), rgba(0,0,0,.35)),
      radial-gradient(ellipse 18% 22% at 80% 18%, #4fbf5a, transparent 70%),
      radial-gradient(ellipse 14% 20% at 66% 10%, #d2c7e6, transparent 70%),
      radial-gradient(ellipse 22% 30% at 18% 65%, #b24ad0, transparent 70%),
      radial-gradient(ellipse 20% 24% at 45% 78%, #7d2fa8, transparent 70%),
      radial-gradient(ellipse 18% 26% at 88% 70%, #9b3fb6, transparent 70%),
      radial-gradient(ellipse 16% 20% at 30% 22%, #8a8ea6, transparent 70%),
      radial-gradient(ellipse 10% 16% at 58% 45%, #e05a8a, transparent 70%),
      linear-gradient(135deg, #2b1f33, #5a3a6e 40%, #3d2a48 70%, #1e1822);
  }
  .hero-title {
    position: absolute; left: 0; width: 1200px; top: 300px; text-align: center;
    font-family: "Oswald", sans-serif; font-weight: 500; font-size: 48px; color: var(--white); letter-spacing: .5px;
  }
  .hero-sub { position: absolute; left: 0; width: 1200px; top: 374px; text-align: center; font-size: 16px; color: #e6e6e6; }
  .hero-btn {
    position: absolute; left: 503px; top: 422px; width: 193px; height: 46px;
    background: rgba(20,20,20,.8); border: 1px solid rgba(255,255,255,.35);
    color: var(--white); font-family: "Oswald", sans-serif; font-size: 15px; letter-spacing: .5px;
    display: flex; align-items: center; justify-content: center;
  }
  .hero-dots { position: absolute; top: 572px; left: 562px; display: flex; gap: 14px; }
  .hero-dots span { width: 8px; height: 8px; border-radius: 50%; background: var(--white); }
  .hero-dots span.active { background: var(--red); }

  /* Background art */
  .backdrop {
    position: absolute; left: 0; top: 612px; width: 1200px; height: 2985px;
    background:
      radial-gradient(ellipse 14% 6% at 10% 4%, #1fa3e0, transparent 70%),
      radial-gradient(ellipse 12% 5% at 90% 3%, #2a7fd8, transparent 70%),
      radial-gradient(ellipse 10% 5% at 6% 14%, #e23a2a, transparent 70%),
      radial-gradient(ellipse 10% 5% at 94% 15%, #e8d23a, transparent 70%),
      radial-gradient(ellipse 12% 5% at 88% 22%, #23b79a, transparent 70%),
      radial-gradient(ellipse 14% 6% at 10% 24%, #f2c02a, transparent 70%),
      radial-gradient(ellipse 18% 8% at 50% 22%, #2f5bd6, transparent 70%),
      radial-gradient(ellipse 12% 6% at 8% 36%, #e07a1a, transparent 70%),
      radial-gradient(ellipse 12% 6% at 92% 35%, #d9a82a, transparent 70%),
      radial-gradient(ellipse 18% 8% at 50% 40%, #c9862a, transparent 70%),
      radial-gradient(ellipse 12% 6% at 6% 50%, #b83a8a, transparent 70%),
      radial-gradient(ellipse 12% 6% at 94% 52%, #3a3fae, transparent 70%),
      radial-gradient(ellipse 14% 6% at 10% 64%, #e0b23a, transparent 70%),
      radial-gradient(ellipse 14% 6% at 92% 66%, #c2407a, transparent 70%),
      radial-gradient(ellipse 12% 6% at 6% 78%, #8c2fc0, transparent 70%),
      radial-gradient(ellipse 12% 6% at 94% 80%, #2a9cd0, transparent 70%),
      radial-gradient(ellipse 14% 6% at 12% 92%, #d83a4a, transparent 70%),
      radial-gradient(ellipse 14% 6% at 88% 94%, #3fb86a, transparent 70%),
      linear-gradient(#2a3580, #5a3a70 20%, #7a4a3a 40%, #5a2f6a 60%, #3a3a88 80%, #4a2a5a);
  }

  /* Panels */
  .panel { position: absolute; left: 229px; width: 731px; background: var(--white); }
  .ribbon { position: absolute; left: 437px; width: 326px; height: 62px; }
  .ribbon-label {
    position: absolute; left: 0; top: 0; width: 326px; height: 52px;
    display: flex; align-items: center; justify-content: center;
    font-family: "Oswald", sans-serif; font-size: 25px; color: var(--white); letter-spacing: .3px;
  }

  .product { position: absolute; width: 220px; text-align: center; }
  .product-art {
    height: 234px; margin: 0 auto;
    background:
      radial-gradient(ellipse 40% 18% at 50% 18%, #e2c24a, transparent 70%),
      radial-gradient(ellipse 50% 25% at 50% 55%, #6a4ab0, transparent 70%),
      linear-gradient(#3a2e6a, #2a2450 45%, #1a1a24 70%, #141414);
  }
  .product-name { font-family: "Oswald", sans-serif; font-size: 17px; margin-top: 30px; color: var(--ink); }
  .product-desc { font-size: 12.5px; line-height: 20px; color: var(--grey); margin: 14px auto 0; width: 200px; }
  .product-price { font-family: "Oswald", sans-serif; font-size: 28px; color: var(--red); margin-top: 22px; }
  .outline-btn {
    display: inline-flex; align-items: center; justify-content: center;
    border: 1.5px solid #333; color: var(--ink); font-family: "Oswald", sans-serif; font-size: 15px;
  }

  .video-main {
    position: absolute; left: 237px; top: 1557px; width: 716px; height: 380px;
    background:
      radial-gradient(ellipse 18% 22% at 70% 18%, #e8e0e0, transparent 70%),
      radial-gradient(ellipse 30% 20% at 25% 20%, #b0202a, transparent 70%),
      radial-gradient(ellipse 40% 30% at 45% 62%, #8a3aa8, transparent 70%),
      radial-gradient(ellipse 20% 20% at 85% 70%, #c8a030, transparent 70%),
      linear-gradient(170deg, #2a1418, #4a2240 40%, #3a3020 75%, #14110e);
  }
  .video-thumb { position: absolute; top: 1973px; height: 138px; }
  .play-label { position: absolute; display: flex; align-items: center; color: var(--white); font-family: "Oswald", sans-serif; white-space: nowrap; }

  .news-art { position: absolute; top: 2390px; width: 224px; height: 187px; }
  .news-meta { position: absolute; top: 2597px; font-family: "Oswald", sans-serif; font-size: 12px; color: var(--ink); }
  .news-title { position: absolute; top: 2630px; width: 224px; font-family: "Oswald", sans-serif; font-size: 13.5px; line-height: 19px; text-transform: uppercase; color: var(--ink); }

  .gallery-art { position: absolute; width: 224px; height: 188px; }

  /* Footer */
  .site-footer { position: absolute; left: 0; top: 3597px; width: 1200px; height: 308px; background: var(--footer); border-top: 4px solid #2a2a2a; }
  .footer-badge { position: absolute; left: 535px; top: 3540px; width: 130px; display: flex; flex-direction: column; align-items: center; gap: 4px; z-index: 3; }
  .footer-col { position: absolute; top: 3663px; list-style: none; }
  .footer-col li { font-family: "Oswald", sans-serif; font-size: 12px; color: var(--white); line-height: 24px; text-transform: uppercase; }
  .social { position: absolute; top: 3669px; left: 743px; display: flex; gap: 6px; }
  .social span { width: 24px; height: 24px; border-radius: 50%; border: 1.5px solid #cfcfcf; }
  .footer-rule { position: absolute; left: 0; top: 3845px; width: 1200px; height: 1px; background: var(--footer-line); }
  .copyright { position: absolute; left: 0; width: 1200px; top: 3866px; text-align: center; font-family: "Oswald", sans-serif; font-size: 10px; color: #cfcfcf; }
</style>
</head>
<body>
<div class="page">

  <header class="site-header">
    <span class="nav-link" style="left:262px">Home</span>
    <span class="nav-link" style="left:320px">About Us</span>
    <span class="nav-link" style="left:402px">Products</span>
    <div class="brand">
      <span class="brand-mark"></span>
      <span class="brand-name">GADGET ARCADE</span>
    </div>
    <span class="nav-link" style="left:694px">FAQ's</span>
    <span class="nav-link" style="left:753px">Support</span>
    <span class="nav-link" style="left:828px">Buy</span>
    <span class="nav-link cart" style="left:905px">
      <svg width="18" height="15" viewBox="0 0 18 15" fill="none" stroke="#fff" stroke-width="1.6">
        <path d="M1 1h3l2 9h9l2-6H5"/><circle cx="7" cy="13" r="1.3" fill="#fff"/><circle cx="14" cy="13" r="1.3" fill="#fff"/>
      </svg>
      My Cart
    </span>
  </header>

  <section class="hero" role="img" aria-label="Close-up photograph of a pinball playfield with purple ramps and green toys"></section>
  <h1 class="hero-title">GADGET ARCADE</h1>
  <p class="hero-sub">We sells pinball machines and accessories</p>
  <span class="hero-btn">SHOP NOW</span>
  <div class="hero-dots"><span class="active"></span><span></span><span></span><span></span></div>

  <div class="backdrop" role="img" aria-label="Blurred colourful pinball backglass artwork"></div>

  <!-- Products -->
  <section class="panel" style="top:718px;height:651px"></section>
  <div class="ribbon" style="top:698px">
    <svg width="326" height="62" viewBox="0 0 326 62">
      <polygon points="0,8 40,8 40,52 0,52 14,30" fill="var(--red-dark)"/>
      <polygon points="326,8 286,8 286,52 326,52 312,30" fill="var(--red-dark)"/>
      <polygon points="28,52 40,52 40,62" fill="var(--red-deep)"/>
      <polygon points="298,52 286,52 286,62" fill="var(--red-deep)"/>
      <rect x="28" y="0" width="270" height="52" fill="var(--red)"/>
    </svg>
    <span class="ribbon-label">OUR PRODUCTS</span>
  </div>

  <div class="product" style="left:254px;top:846px">
    <div class="product-art" style="width:96px" role="img" aria-label="Gadget Arcade pinball machine 1, front view"></div>
    <div class="product-name">GADGET ARCADE 1</div>
    <p class="product-desc">Sed ut perspiciatis unde omnis iste natus error sit voluptatem</p>
    <div class="product-price">$7000/-</div>
    <span class="outline-btn" style="width:135px;height:37px;margin-top:16px">SHOP NOW</span>
  </div>
  <div class="product" style="left:489px;top:846px">
    <div class="product-art" style="width:160px" role="img" aria-label="Gadget Arcade pinball machine 2, angled view"></div>
    <div class="product-name">GADGET ARCADE 2</div>
    <p class="product-desc">Sed ut perspiciatis unde omnis iste natus error sit voluptatem</p>
    <div class="product-price">$7000/-</div>
    <span class="outline-btn" style="width:135px;height:37px;margin-top:16px">SHOP NOW</span>
  </div>
  <div class="product" style="left:726px;top:846px">
    <div class="product-art" style="width:150px" role="img" aria-label="Gadget Arcade pinball machine 3, angled view"></div>
    <div class="product-name">GADGET ARCADE 3</div>
    <p class="product-desc">Sed ut perspiciatis unde omnis iste natus error sit voluptatem</p>
    <div class="product-price">$7000/-</div>
    <span class="outline-btn" style="width:135px;height:37px;margin-top:16px">SHOP NOW</span>
  </div>

  <!-- Videos -->
  <section class="panel" style="top:1484px;height:682px"></section>
  <div class="ribbon" style="top:1447px">
    <svg width="326" height="62" viewBox="0 0 326 62">
      <polygon points="0,8 40,8 40,52 0,52 14,30" fill="var(--red-dark)"/>
      <polygon points="326,8 286,8 286,52 326,52 312,30" fill="var(--red-dark)"/>
      <polygon points="28,52 40,52 40,62" fill="var(--red-deep)"/>
      <polygon points="298,52 286,52 286,62" fill="var(--red-deep)"/>
      <rect x="28" y="0" width="270" height="52" fill="var(--red)"/>
    </svg>
    <span class="ribbon-label">OUR VIDEOS</span>
  </div>

  <div class="video-main" role="img" aria-label="Video still of an arcade showroom with a lit purple pinball playfield"></div>
  <div class="play-label" style="left:248px;top:1868px;gap:14px;font-size:16px">
    <svg width="56" height="56" viewBox="0 0 56 56"><circle cx="28" cy="28" r="25" fill="none" stroke="#fff" stroke-width="3"/><polygon points="22,17 40,28 22,39" fill="#fff"/></svg>
    GADGET ARCADE 1 VIDEOS
  </div>

  <div class="video-thumb" style="left:237px;width:224px;background:radial-gradient(ellipse 40% 40% at 40% 40%,#d04aa0,transparent 70%),radial-gradient(ellipse 30% 30% at 75% 30%,#e8c23a,transparent 70%),linear-gradient(150deg,#2a2a60,#4a2a70 50%,#1a1a2a)" role="img" aria-label="Video still of a colourful pinball playfield"></div>
  <div class="video-thumb" style="left:484px;width:221px;background:radial-gradient(ellipse 35% 40% at 50% 35%,#8a8aa0,transparent 70%),radial-gradient(ellipse 30% 30% at 30% 70%,#c8a030,transparent 70%),linear-gradient(150deg,#1a1a24,#3a3450 50%,#141414)" role="img" aria-label="Video still of a pinball cabinet"></div>
  <div class="video-thumb" style="left:729px;width:224px;background:radial-gradient(ellipse 40% 45% at 60% 40%,#c0202a,transparent 70%),radial-gradient(ellipse 25% 30% at 20% 60%,#e0c090,transparent 70%),linear-gradient(150deg,#3a0e12,#6a1a22 50%,#1a0a0c)" role="img" aria-label="Video still of a red pinball cabinet"></div>
  <div class="play-label" style="left:244px;top:2076px;gap:6px;font-size:8px">
    <svg width="28" height="28" viewBox="0 0 28 28"><circle cx="14" cy="14" r="12" fill="none" stroke="#fff" stroke-width="2"/><polygon points="11,8 20,14 11,20" fill="#fff"/></svg>GADGET ARCADE 1 VIDEOS
  </div>
  <div class="play-label" style="left:491px;top:2076px;gap:6px;font-size:8px">
    <svg width="28" height="28" viewBox="0 0 28 28"><circle cx="14" cy="14" r="12" fill="none" stroke="#fff" stroke-width="2"/><polygon points="11,8 20,14 11,20" fill="#fff"/></svg>GADGET ARCADE 1 VIDEOS
  </div>
  <div class="play-label" style="left:736px;top:2076px;gap:6px;font-size:8px">
    <svg width="28" height="28" viewBox="0 0 28 28"><circle cx="14" cy="14" r="12" fill="none" stroke="#fff" stroke-width="2"/><polygon points="11,8 20,14 11,20" fill="#fff"/></svg>GADGET ARCADE 1 VIDEOS
  </div>

  <!-- News -->
  <section class="panel" style="top:2296px;height:497px"></section>
  <div class="ribbon" style="top:2260px">
    <svg width="326" height="62" viewBox="0 0 326 62">
      <polygon points="0,8 40,8 40,52 0,52 14,30" fill="var(--red-dark)"/>
      <polygon points="326,8 286,8 286,52 326,52 312,30" fill="var(--red-dark)"/>
      <polygon points="28,52 40,52 40,62" fill="var(--red-deep)"/>
      <polygon points="298,52 286,52 286,62" fill="var(--red-deep)"/>
      <rect x="28" y="0" width="270" height="52" fill="var(--red)"/>
    </svg>
    <span class="ribbon-label">OUR NEWS</span>
  </div>

  <div class="news-art" style="left:237px;background:radial-gradient(ellipse 40% 30% at 50% 45%,#f0d23a,transparent 70%),radial-gradient(ellipse 30% 30% at 20% 25%,#e03a2a,transparent 70%),radial-gradient(ellipse 30% 30% at 80% 75%,#2a7ad8,transparent 70%),linear-gradient(140deg,#d0522a,#c93a8a 45%,#3a2a7a)" role="img" aria-label="Photo of a colourful pinball playfield"></div>
  <div class="news-art" style="left:484px;background:radial-gradient(ellipse 30% 35% at 55% 30%,#9a9aa8,transparent 70%),radial-gradient(ellipse 40% 25% at 45% 80%,#5a4a8a,transparent 70%),linear-gradient(140deg,#1a1a1e,#3a3a44 50%,#121212)" role="img" aria-label="Photo of a player at a pinball machine"></div>
  <div class="news-art" style="left:729px;background:radial-gradient(ellipse 40% 35% at 40% 35%,#c07a5a,transparent 70%),radial-gradient(ellipse 40% 35% at 70% 75%,#3a6ab0,transparent 70%),linear-gradient(140deg,#5a3a30,#2a3a5a 50%,#16161c)" role="img" aria-label="Photo of a technician servicing pinball electronics"></div>

  <span class="news-meta" style="left:237px">MARCH 2017</span>
  <span class="news-meta" style="left:484px">MARCH 2017</span>
  <span class="news-meta" style="left:729px">MARCH 2017</span>
  <p class="news-title" style="left:237px">Sed ut perspiciatis unde omnis iste natus error sit voluptatem accusantium doloremque</p>
  <p class="news-title" style="left:484px">Sed ut perspiciatis unde omnis iste natus error sit voluptatem accusantium doloremque</p>
  <p class="news-title" style="left:729px">Sed ut perspiciatis unde omnis iste natus error sit voluptatem accusantium doloremque</p>
  <span class="outline-btn abs" style="left:237px;top:2710px;width:109px;height:29px;font-size:12px">READ MORE</span>
  <span class="outline-btn abs" style="left:484px;top:2710px;width:109px;height:29px;font-size:12px">READ MORE</span>
  <span class="outline-btn abs" style="left:729px;top:2710px;width:109px;height:29px;font-size:12px">READ MORE</span>

  <!-- Gallery -->
  <section class="panel" style="top:2921px;height:572px"></section>
  <div class="ribbon" style="top:2879px">
    <svg width="326" height="62" viewBox="0 0 326 62">
      <polygon points="0,8 40,8 40,52 0,52 14,30" fill="var(--red-dark)"/>
      <polygon points="326,8 286,8 286,52 326,52 312,30" fill="var(--red-dark)"/>
      <polygon points="28,52 40,52 40,62" fill="var(--red-deep)"/>
      <polygon points="298,52 286,52 286,62" fill="var(--red-deep)"/>
      <rect x="28" y="0" width="270" height="52" fill="var(--red)"/>
    </svg>
    <span class="ribbon-label">OUR GALLERY</span>
  </div>

  <div class="gallery-art" style="left:237px;top:3014px;background:radial-gradient(ellipse 40% 30% at 50% 20%,#e0a040,transparent 70%),radial-gradient(ellipse 40% 35% at 40% 70%,#4a6a9a,transparent 70%),linear-gradient(140deg,#5a3a2a,#3a4a5a 50%,#1e1e22)" role="img" aria-label="Players in an arcade hall"></div>
  <div class="gallery-art" style="left:484px;top:3014px;background:radial-gradient(ellipse 35% 35% at 50% 50%,#f0a030,transparent 70%),radial-gradient(ellipse 25% 25% at 20% 25%,#e05020,transparent 70%),linear-gradient(140deg,#2a0e06,#a04a14 50%,#2a1006)" role="img" aria-label="Glowing pinball playfield detail"></div>
  <div class="gallery-art" style="left:729px;top:3014px;background:radial-gradient(ellipse 40% 35% at 40% 40%,#8a7ad0,transparent 70%),radial-gradient(ellipse 30% 30% at 75% 70%,#d0d0e0,transparent 70%),linear-gradient(140deg,#3a3a8a,#5a4aa0 50%,#22224a)" role="img" aria-label="Pinball cabinet controls close-up"></div>
  <div class="gallery-art" style="left:237px;top:3220px;background:radial-gradient(ellipse 20% 45% at 50% 45%,#e8e8f0,transparent 70%),radial-gradient(ellipse 25% 40% at 15% 50%,#c03a4a,transparent 70%),radial-gradient(ellipse 25% 40% at 85% 50%,#3a5ac0,transparent 70%),linear-gradient(140deg,#3a3a4a,#6a6070 50%,#2a2a34)" role="img" aria-label="Row of pinball machines in an arcade"></div>
  <div class="gallery-art" style="left:484px;top:3220px;background:radial-gradient(ellipse 35% 30% at 50% 45%,#f0c070,transparent 70%),radial-gradient(ellipse 30% 30% at 25% 75%,#d04020,transparent 70%),linear-gradient(140deg,#3a1008,#b0601e 50%,#2a0e08)" role="img" aria-label="Lit pinball bumpers close-up"></div>
  <div class="gallery-art" style="left:729px;top:3220px;background:radial-gradient(ellipse 40% 30% at 40% 20%,#e02a3a,transparent 70%),radial-gradient(ellipse 30% 30% at 75% 60%,#f0c040,transparent 70%),linear-gradient(140deg,#8a1a2a,#c84a5a 50%,#4a3a5a)" role="img" aria-label="Arcade storefront on a city street"></div>

  <svg class="abs" style="left:578px;top:3432px" width="44" height="18" viewBox="0 0 44 18" fill="none" stroke="#222" stroke-width="2.5">
    <path d="M9 2 2 9l7 7"/><path d="M35 2l7 7-7 7"/>
  </svg>

  <!-- Footer -->
  <footer class="site-footer"></footer>
  <div class="footer-badge">
    <span class="brand-mark" style="width:58px;height:58px"></span>
    <span class="brand-name">GADGET ARCADE</span>
  </div>
  <ul class="footer-col" style="left:263px">
    <li>Home</li><li>About Us</li><li>Products</li><li>FAQ's</li><li>Support</li><li>Buy</li>
  </ul>
  <ul class="footer-col" style="left:427px">
    <li>Terms of Service</li><li>Privacy Policy</li><li>Help</li><li>Disclaimer</li>
  </ul>
  <ul class="footer-col" style="left:594px">
    <li>Order Tracker</li><li>Returns</li><li>Customer Care</li><li>Community</li>
  </ul>
  <div class="social"><span></span><span></span><span></span><span></span><span></span><span></span></div>
  <div class="footer-rule"></div>
  <p class="copyright">© 2017 COMPANY NAME | ALL RIGHTS RESERVED</p>

</div>
</body>
</html>
```